Corporate Business Card

Very professional, Modern, Not to busy, include phone address email, website
(360) 617-4930, 18761 52nd Avenue S, Corvane, OR 98047, martin@plumlinegroup.com, varkoworks.com

Target Market(s)

Manufacturing

Industry/Entity Type

Aero, machining, manufacturing, Off road racing

Contact Information for Business Card

Phone, address email, website

```html
<!DOCTYPE html>
<html lang="en">
<head>
<meta charset="utf-8">
<title>Varko Works — Business Card</title>
<link rel="stylesheet" href="https://fonts.googleapis.com/css2?family=Saira:wght@400;600;700&display=swap">
<style>
  :root {
    --navy: #16356b;
    --navy-light: #1b4183;
    --red: #d3232c;
    --white: #ffffff;
    --backdrop: #dadada;
    --card-w: 366px;
    --card-h: 594px;
  }
  * { box-sizing: border-box; margin: 0; padding: 0; }
  html, body {
    width: 1200px;
    height: 1200px;
    overflow: hidden;
    background: var(--backdrop);
    font-family: "Saira", sans-serif;
  }
  .canvas {
    position: relative;
    width: 1200px;
    height: 1200px;
  }
  .card {
    position: absolute;
    top: 303px;
    width: var(--card-w);
    height: var(--card-h);
  }
  .card--front {
    left: 200px;
    background: var(--navy);
    overflow: hidden;
  }
  .card--back {
    left: 634px;
    background: var(--white);
    color: var(--navy);
    text-align: center;
  }
  .front-texture {
    position: absolute;
    inset: 0;
    background: linear-gradient(135deg, var(--navy) 0%, var(--navy-light) 50%, var(--navy) 100%);
  }
  .brand-name {
    position: absolute;
    left: 0;
    right: 0;
    text-align: center;
    font-family: "Saira", sans-serif;
    font-weight: 700;
    font-size: 38px;
    letter-spacing: 1px;
    white-space: nowrap;
  }
  .card--front .brand-name {
    top: 475px;
    color: var(--white);
  }
  .card--back .brand-name {
    top: 146px;
    color: var(--navy);
  }
  .contact {
    position: absolute;
    left: 0;
    right: 0;
    top: 378px;
    font-size: 18.5px;
    font-weight: 400;
    line-height: 26px;
  }
  .contact .web-domain { color: var(--red); }
  .divider {
    width: 137px;
    height: 1px;
    background: var(--navy);
    margin: 13px auto 9px;
  }
</style>
</head>
<body>
  <main class="canvas">
    <section class="card card--front">
      <div class="front-texture" role="img" aria-label="Faint diagonal brand pattern on navy background"></div>
      <div class="brand-name">VARKO WORKS</div>
    </section>

    <section class="card card--back">
      <div class="brand-name">VARKO WORKS</div>
      <div class="contact">
        <p class="contact-phone">(360) 617-4930</p>
        <p class="contact-email">martin@plumlinegroup.com</p>
        <p class="contact-web">www.<span class="web-domain">varkoworks</span>.com</p>
        <div class="divider"></div>
        <p class="contact-address">18761 52nd Avenue S</p>
        <p class="contact-city">Corvane, OR 98047</p>
      </div>
    </section>
  </main>
</body>
</html>
```